Vernac Law Business cards and stationary design project

We are looking for a stationary design for business cards (double sided), 8x10, 5x7, and legal and standard envelopes.

We would like the design to match the logo that we have already.
Color palate preferred is Teal, White, grey and any others that will look good for a professional law firm.

We would like this statement: "RELATIONSHIPS. RESPECT. RESULT" to be on the back of the business cards and maybe on the stationary if it looks good.

Please see link to website for more information: www.vernac-law.example

Target Market(s)

Potential clients that need Attorney services.

Industry/Entity Type

Law Firm

Contact Information for Business Card

We would like the front and back to be two different colors. Current business cards are teal front, grey back and are a vertical design. We are open to options with colors.

Font styles to use
Serif

Colors
33a6d7
33b8a4
b9b9b9
5c5c5c

Requirements
Must have
• Logo supplied needs to go on the card and stationary.
• Match website color palate, www.vernac-law.example
• Be professional and not too wordy.
• Criminal Law, Civil Litigation, Personal Injury, Restraining Orders need to be on the card.
Nice to have
• RELATIONSHIPS. RESPECT. RESULTS. on the back of the card.
Should not have
• Not be too busy/wordy or too flashy.

```html
<!DOCTYPE html>
<html lang="en">
<head>
<meta charset="utf-8">
<title>Vernac Law – Business Card</title>
<link rel="stylesheet" href="https://fonts.googleapis.com/css2?family=Cinzel:wght@400;600&family=Crimson+Text:wght@400&display=swap">
<style>
  :root {
    --teal: #12889a;
    --white: #ffffff;
    --grey: #9a9a9a;
    --backdrop: #3c3c3c;
  }
  * { margin: 0; padding: 0; box-sizing: border-box; }
  html, body { width: 1105px; height: 1200px; overflow: hidden; }
  body { background: var(--backdrop); position: relative; }

  .card {
    position: absolute;
    left: 196px;
    width: 720px;
    height: 410px;
    overflow: hidden;
  }
  .card--front { top: 146px; background: var(--white); }
  .card--back { top: 602px; background: var(--teal); }

  .front-bands { position: absolute; left: 0; top: 0; }

  .wordmark {
    position: absolute;
    left: 462px;
    width: 222px;
    top: 62px;
    display: flex;
    flex-direction: column;
    align-items: center;
    gap: 18px;
  }
  .wordmark__dot {
    width: 56px; height: 56px;
    border-radius: 50%;
    background: var(--teal);
  }
  .wordmark__name {
    font-family: "Cinzel", serif;
    font-weight: 400;
    font-size: 31px;
    color: var(--teal);
    white-space: nowrap;
  }

  .holder {
    position: absolute;
    left: 39px;
    top: 300px;
    font-family: "Cinzel", serif;
    color: var(--white);
    white-space: nowrap;
  }
  .holder__name { font-size: 30px; font-weight: 600; }
  .holder__role { font-size: 21px; font-weight: 400; }

  .contacts {
    position: absolute;
    left: 34px;
    top: 355px;
    display: flex;
    gap: 26px;
    font-family: "Crimson Text", serif;
    font-size: 19px;
    color: var(--white);
    white-space: nowrap;
  }
  .contact { display: flex; align-items: center; gap: 8px; }
  .contact svg { width: 16px; height: 16px; fill: var(--white); }

  .back-name {
    position: absolute;
    left: 0; right: 0;
    top: 140px;
    text-align: center;
    font-family: "Cinzel", serif;
    font-weight: 400;
    font-size: 54px;
    color: var(--white);
  }
  .motto {
    position: absolute;
    left: 0; right: 0;
    top: 317px;
    text-align: center;
    font-family: "Crimson Text", serif;
    font-size: 21px;
    letter-spacing: 0.5px;
    color: var(--white);
  }
  .services {
    position: absolute;
    left: 0; right: 0;
    top: 351px;
    text-align: center;
    font-family: "Crimson Text", serif;
    font-size: 20px;
    color: var(--white);
    white-space: pre;
  }
</style>
</head>
<body>
  <section class="card card--front">
    <svg class="front-bands" width="720" height="410" viewBox="0 0 720 410" aria-hidden="true">
      <polygon points="0,293 453,293 482,330 720,330 720,410 0,410" fill="var(--teal)"/>
      <polygon points="461,307 720,307 720,326 476,326" fill="var(--grey)"/>
    </svg>

    <div class="wordmark">
      <span class="wordmark__dot"></span>
      <span class="wordmark__name">Vernac Law</span>
    </div>

    <div class="holder">
      <span class="holder__name">Nora Vernac</span>
      <span class="holder__role"> - Trial Lawyer</span>
    </div>

    <div class="contacts">
      <span class="contact">
        <svg viewBox="0 0 16 16" aria-hidden="true"><path d="M3.6 1.2 5.8 3.4c.4.4.4 1 0 1.4L4.7 5.9c.8 1.8 2.2 3.2 4 4l1.1-1.1c.4-.4 1-.4 1.4 0l2.2 2.2c.4.4.4 1 0 1.4l-1.3 1.3c-.7.7-1.8.8-2.7.4C5.8 12.6 3.4 10.2 1.9 6.6c-.4-.9-.3-2 .4-2.7z"/></svg>
        (555) 014-2738
      </span>
      <span class="contact">
        <svg viewBox="0 0 16 16" aria-hidden="true"><path d="M1 3.5h14v1L8 9 1 4.5z"/><path d="M1 6l7 4.5L15 6v6.5H1z"/></svg>
        nora@vernac-law.example
      </span>
      <span class="contact">
        <svg viewBox="0 0 16 16" aria-hidden="true"><circle cx="8" cy="8" r="7"/><path d="M5 4.5c1 .3 1.6 1 1.3 2-.3.8-1.5.8-1.6 1.8 0 .9 1 1.3.9 2.4-.1.8-.6 1.3-.9 1.6M10.5 3c-.5 1 .4 1.6 1.3 1.8.9.2 1.4.9 1.1 1.8-.3.8-1.3.8-1.6 1.6-.3.9.5 1.6.2 2.6" stroke="var(--teal)" stroke-width="1.2" fill="none"/></svg>
        www.vernac-law.example
      </span>
    </div>
  </section>

  <section class="card card--back">
    <div class="back-name">Vernac Law</div>
    <p class="motto">RELATIONSHIPS. RESPECT. RESULTS.</p>
    <p class="services">Criminal Law,  Civil Litigation/Personal Injury, Restraining</p>
  </section>
</body>
</html>
```